New Fitness Company looking for creative website design

I am building a new fitness matching service. To match customers looking for fitness services to professionals that meet their requirements

My business will have 5 different divisions and I would like to have tabs for each division

1. Matching client to trainer - I need to have video upload capability on the site
2. Corporate personal training services

-The site needs a shopping cart as well as payment capability.
- I am looking for the site to be bright and inviting as well as have clients and trainers going through some type of workout on the main page.
- I also need the capability to capture email addresses
- We are going to have a section that ask the customer questions to match up the trainer so that needs to be a part of the site
-Ability to have trainers rated in a 1 star to 5 stars as well as reviews
- Site should be inviting, bright and vibrant colors that catch the eye and is easy to use
- Similar sites for inspiration are www.zavrello.com where you give a description of how the service works, short video and various services.

Target Market(s)

mid income to high income, mix of female and male customers

Industry/Entity Type

Fitness

Coding

Coded - Design and coding required

Number of Pages Required

5+ page

Font styles to use
Serif
Sans Serif

Requirements
Must have
• Must have the logos that I provided in the website
Should not have
• Not looking for bodybuilders on website. This is for everyday people that are interested in staying in shape and working out. So active fit people will resonate with my prospects

```html
<!DOCTYPE html>
<html lang="en">
<head>
<meta charset="utf-8">
<title>Brisko Fitness</title>
<link rel="stylesheet" href="https://fonts.googleapis.com/css2?family=Roboto:wght@300;400;500;700&family=Open+Sans:wght@400;600&display=swap">
<style>
:root{
  --green:#3fb950;
  --green-band:#4cbf62;
  --orange:#f0a020;
  --blue:#2a8fd6;
  --ink:#222;
  --body:#666;
  --muted:#999;
  --rule:#e6e6e6;
  --dark:#1c1f1d;
  --white:#fff;
}
*{box-sizing:border-box;margin:0;padding:0}
html,body{width:1200px;height:3103px;overflow:hidden}
body{font-family:'Open Sans',Arial,sans-serif;color:var(--body);background:var(--white);position:relative}
section,footer{position:absolute;left:0;width:1200px}

/* hero */
.hero{top:0;height:625px;background:linear-gradient(100deg,#3a3a36 0%,#5b5449 35%,#2c2e2e 65%,#1d2021 100%);overflow:hidden}
.hero-photo{position:absolute;inset:0;background:radial-gradient(ellipse at 40% 40%,rgba(196,150,110,.35),transparent 55%),radial-gradient(ellipse at 75% 50%,rgba(150,120,100,.25),transparent 50%)}
.brand{position:absolute;left:100px;top:40px;display:flex;align-items:center;gap:12px;color:var(--white);font-family:'Roboto',sans-serif;font-weight:700;font-size:34px;letter-spacing:2px}
.brand-dot{width:26px;height:26px;border-radius:50%;background:var(--white)}
.nav{position:absolute;right:100px;top:46px;display:flex;gap:42px;font-family:'Roboto',sans-serif;font-size:13px;color:var(--white);font-weight:500}
.hero-title{position:absolute;top:338px;width:100%;text-align:center;color:var(--white);font-family:'Roboto',sans-serif;font-weight:500;font-size:48px}
.hero-sub{position:absolute;top:400px;width:100%;text-align:center;color:var(--white);font-family:'Roboto',sans-serif;font-size:15px;font-weight:500}
.dots{position:absolute;top:455px;width:100%;display:flex;justify-content:center;gap:10px}
.dots span{width:14px;height:14px;border-radius:50%;background:var(--white)}
.dots .on{background:var(--orange);box-shadow:0 0 0 3px rgba(255,255,255,.8)}

/* corporate */
.corporate{top:625px;height:505px}
.section-title{font-family:'Roboto',sans-serif;font-size:30px;color:var(--ink);text-align:center;font-weight:400}
.section-title em{font-style:normal;color:var(--green)}
.corporate .section-title{position:absolute;top:56px;width:100%}
.divider{position:absolute;top:104px;left:495px;width:210px;height:24px}
.intro{position:absolute;top:140px;left:150px;width:900px;text-align:center;font-size:11.5px;line-height:22px;color:var(--body)}
.cards{position:absolute;top:217px;left:100px;display:flex;gap:16px}
.card{width:238px;height:219px;position:relative;border:3px solid #eee}
.card .ph{position:absolute;inset:0}
.card .label{position:absolute;left:20px;bottom:48px;background:rgba(255,255,255,.85);padding:4px 10px;font-size:15px;color:#444;width:150px}
.card .trainer{position:absolute;left:20px;bottom:16px;background:var(--orange);color:var(--white);font-size:12px;padding:5px 10px}

/* welcome band */
.welcome{top:1130px;height:380px;background:linear-gradient(180deg,#5cc86f,#44b85a)}
.welcome .section-title{position:absolute;top:92px;width:100%;color:var(--white);font-size:38px}
.welcome p{position:absolute;top:160px;left:130px;width:940px;text-align:center;color:var(--white);font-size:11.5px;line-height:21px}
.btn-ghost{position:absolute;top:252px;left:530px;width:138px;height:40px;border:2px solid rgba(255,255,255,.8);border-radius:3px;color:var(--white);font-size:12px;display:flex;align-items:center;justify-content:center;gap:8px}

/* rating + video */
.rating{top:1510px;height:466px}
.col-title{position:absolute;font-family:'Roboto',sans-serif;font-size:21px;font-weight:400;color:#333}
.rating .left{position:absolute;left:100px;top:66px;width:520px}
.rating .left .col-title{position:static;padding-bottom:20px;border-bottom:1px solid var(--rule)}
.review{display:flex;gap:26px;margin-top:28px}
.review+.review{margin-top:26px}
.avatar{width:104px;height:104px;border-radius:50%;border:4px solid #eee;background:linear-gradient(135deg,#b08a70,#6e5446);flex:none}
.review h4{font-family:'Open Sans',sans-serif;font-weight:400;font-size:13.5px;color:#444;margin-top:2px}
.meta{display:flex;gap:20px;align-items:center;margin:10px 0 8px;font-size:10px;color:var(--blue);font-weight:400}
.review p{font-size:12px;line-height:21px;color:var(--body)}
.rating .right{position:absolute;left:695px;top:66px;width:405px}
.rating .right .col-title{position:static}
.video{margin-top:32px;width:405px;height:284px;position:relative;border:1px solid #ddd}
.video .ph{position:absolute;left:0;top:0;right:0;height:256px;background:linear-gradient(120deg,#7c92a8,#c0c8cf 45%,#3f7fbf)}
.play{position:absolute;left:172px;top:100px;width:60px;height:60px;border-radius:50%;background:rgba(30,30,30,.6);border:3px solid rgba(255,255,255,.85)}
.controls{position:absolute;left:0;right:0;bottom:0;height:28px;background:#f4f4f4;display:flex;align-items:center;padding:0 10px;gap:12px;font-size:9px;color:#555}
.track{flex:1;height:4px;background:#ccc;position:relative}
.track i{position:absolute;left:0;top:0;height:4px;width:70%;background:#d4453c}
.vol{width:44px;height:4px;background:#d4453c}

/* products */
.products{top:1976px;height:490px;background:linear-gradient(100deg,#3a3f3c,#6a5f56 40%,#807062 60%,#3d4240)}
.products .col-title{left:100px;top:58px;color:var(--white);font-size:23px}
.arrows{position:absolute;right:100px;top:58px;display:flex;gap:6px}
.arrows span{width:26px;height:26px;border-radius:50%;border:1px solid var(--white);display:flex;align-items:center;justify-content:center}
.shelf{position:absolute;left:100px;top:124px;width:1000px;height:306px;background:var(--white);display:flex;gap:23px;padding:26px}
.product{width:219px}
.product .ph{height:170px;border:1px solid #e8e8e8;box-shadow:0 1px 4px rgba(0,0,0,.08);background:linear-gradient(180deg,#f7f7f7,#ececec)}
.product .row{display:flex;justify-content:space-between;align-items:center;margin-top:16px;font-size:12.5px;color:#555}
.product .row.sub{margin-top:6px}
.price{color:var(--blue);font-size:17px;font-family:'Roboto',sans-serif}
.old{font-size:11px;color:#777;text-decoration:line-through}

/* faq */
.faq{top:2466px;height:321px}
.faq .col-title{left:100px;top:50px;font-size:23px}
.faq-cols{position:absolute;left:100px;top:112px;display:flex;gap:50px}
.faq-item{width:300px;border-bottom:1px solid var(--rule);padding-bottom:20px}
.faq-item h4{font-weight:400;color:var(--blue);font-size:15px;margin-bottom:12px}
.faq-item p{font-size:11.5px;line-height:22px;color:var(--body)}
.more{margin-top:12px;display:flex;align-items:center;gap:6px;font-size:11px;color:#444}

/* footer */
.footer{top:2787px;height:257px;background:linear-gradient(180deg,#1a1d1b,#2b3530)}
.footer .brand{left:124px;top:28px;font-size:28px}
.contact{position:absolute;top:38px;display:flex;gap:14px;color:var(--white);font-size:13px;line-height:20px}
.ic{width:34px;height:34px;border-radius:50%;border:1px solid #888;display:flex;align-items:center;justify-content:center;flex:none}
.footer .rule{position:absolute;left:100px;right:100px;top:104px;border-top:1px solid #3a3f3c}
.newsletter{position:absolute;left:118px;top:130px;color:var(--white);font-family:'Roboto',sans-serif;font-size:14px}
.email{position:absolute;left:118px;top:170px;width:330px;height:42px;border:1px solid #aaa;display:flex;align-items:center;justify-content:space-between;padding:0 14px;color:var(--white);font-size:11px}
.links{position:absolute;left:582px;top:148px;color:var(--white);font-size:11px;display:flex;gap:8px}
.social{position:absolute;left:582px;top:180px;display:flex;gap:6px}
.social span{width:24px;height:24px;border-radius:50%;border:1px solid #ccc}
.copy{position:absolute;left:0;width:1200px;top:3044px;height:59px;background:var(--green);color:var(--white);font-size:11px;display:flex;align-items:center;justify-content:center}
</style>
</head>
<body>

<svg width="0" height="0" style="position:absolute"><defs><path id="s" d="M5.5 0 7 3.8 11 4 8 6.6 9 10.6 5.5 8.4 2 10.6 3 6.6 0 4 4 3.8z"/></defs></svg>

<section class="hero">
  <div class="hero-photo" role="img" aria-label="Photo of a woman and a man running on treadmills in a gym"></div>
  <div class="brand"><span class="brand-dot"></span>BRISKO</div>
  <nav class="nav"><span>HOME</span><span>ABOUT US</span><span>PERSONAL TRAINING</span><span>BLOG</span><span>FAQ</span><span>CONTACT</span></nav>
  <h1 class="hero-title">BRISKO FITNESS</h1>
  <p class="hero-sub">NEMO ENIM IPSAM VOLUPTATEM QUIA VOLUPTAS SIT ASPERNATUR</p>
  <div class="dots"><span class="on"></span><span></span><span></span><span></span></div>
</section>

<section class="corporate">
  <h2 class="section-title">CORPORATE <em>PERSONAL</em> TRAINING</h2>
  <svg class="divider" viewBox="0 0 210 24"><line x1="0" y1="12" x2="90" y2="12" stroke="#3fb950"/><line x1="120" y1="12" x2="210" y2="12" stroke="#3fb950"/><circle cx="105" cy="13" r="7" fill="none" stroke="#3fb950" stroke-width="2"/></svg>
  <p class="intro">Vestibulum commodo volutpat a, convallis ac, laoreet enim. Phasellus fermentum in, dolor pellentesque. Mulla imperdiet sit amet magna. Vestibulum dapibus. Vestibm commodo volutpat a, convallis ac, laoreet enim. Phasellus fermentum in, dolor pellentesque. Mulla imperdiet sit amet magna.</p>
  <div class="cards">
    <div class="card"><div class="ph" role="img" aria-label="Group workout with exercise balls" style="background:linear-gradient(135deg,#3e4f8a,#8a6a5a)"></div><div class="label">Nemo enim ipsam</div><div class="trainer">Trainer John Doe</div></div>
    <div class="card"><div class="ph" role="img" aria-label="People doing planks in a studio" style="background:linear-gradient(135deg,#c7b9a8,#4a5b8a)"></div><div class="label">Nemo enim ipsam</div><div class="trainer">Trainer John Doe</div></div>
    <div class="card"><div class="ph" role="img" aria-label="Trainer and client in a bright office gym" style="background:linear-gradient(135deg,#8aa0b8,#5a6670)"></div><div class="label">Nemo enim ipsam</div><div class="trainer">Trainer John Doe</div></div>
    <div class="card"><div class="ph" role="img" aria-label="Man and woman running outdoors" style="background:linear-gradient(135deg,#e8e3dc,#d46a8a)"></div><div class="label">Nemo enim ipsam</div><div class="trainer">Trainer John Doe</div></div>
  </div>
</section>

<section class="welcome" role="img" aria-label="Green tinted photo of a person meditating by the sea">
  <h2 class="section-title">WELCOME TO BRISKO</h2>
  <p>Lorem ipsum dolor sit amet, consectetur adipiscing elit, sed do eiusmod tempor incididunt ut labore et dolore magna aliqua. Ut enim ad minim veniam, quis nostrud exercitation ullamco laboris nisi ut aliquip ex ea commodo consequat. Duis aute irure dolor in reprehenderit in voluptate velit esse cillum dolore eu fugiat nulla pariatur. Lorem ipsum dolor sit amet, consectetur adipiscing elit, sed do eiusmod tempor incididunt ut labore et dolore magna aliqua. Ut enim ad minim veniam, quis nostrud.</p>
  <div class="btn-ghost">READ MORE <svg width="12" height="12" viewBox="0 0 12 12"><circle cx="6" cy="6" r="6" fill="#fff"/><path d="M5 3.5 7.5 6 5 8.5" stroke="#4cbf62" stroke-width="1.5" fill="none"/></svg></div>
</section>

<section class="rating">
  <div class="left">
    <h3 class="col-title">TRAINER RATING</h3>
    <div class="review">
      <div class="avatar" role="img" aria-label="Portrait of a smiling woman"></div>
      <div>
        <h4>Nemo Enim Ipsam Voluptatem</h4>
        <div class="meta">3 MINUTES AGO <svg width="60" height="11" viewBox="0 0 60 11"><g fill="#f0a020"><use href="#s"/><use href="#s" x="12"/><use href="#s" x="24"/></g><g fill="#ddd"><use href="#s" x="36"/><use href="#s" x="48"/></g></svg></div>
        <p>Lorem ipsum dolor sit amet, consectetur adipiscing elit, sed do eiusmod tempor incididunt ut labore et dolore magna aliqua. Ut enim ad minim veniam, quis nostrud</p>
      </div>
    </div>
    <div class="review">
      <div class="avatar" role="img" aria-label="Portrait of a smiling man"></div>
      <div>
        <h4>Nemo Enim Ipsam Voluptatem</h4>
        <div class="meta">3 MINUTES AGO <svg width="60" height="11" viewBox="0 0 60 11"><g fill="#f0a020"><use href="#s"/><use href="#s" x="12"/><use href="#s" x="24"/></g><g fill="#ddd"><use href="#s" x="36"/><use href="#s" x="48"/></g></svg></div>
        <p>Lorem ipsum dolor sit amet, consectetur adipiscing elit, sed do eiusmod tempor incididunt ut labore et dolore magna aliqua. Ut enim ad minim veniam, quis nostrud</p>
      </div>
    </div>
  </div>
  <div class="right">
    <h3 class="col-title">MATCHING CLIENT TO TRAINER</h3>
    <div class="video">
      <div class="ph" role="img" aria-label="Video still of a trainer with a clipboard in a gym"></div>
      <svg class="play" viewBox="0 0 60 60"><path d="M24 18 42 30 24 42z" fill="#fff"/></svg>
      <div class="controls"><span>▶</span><span>00:00/03:02</span><div class="track"><i></i></div><span>◀)</span><div class="vol"></div></div>
    </div>
  </div>
</section>

<section class="products" role="img" aria-label="Blurred photo of smiling people exercising">
  <h3 class="col-title">SELLING FITNESS PRODUCTS</h3>
  <div class="arrows"><span><svg width="8" height="10"><path d="M6 1 2 5 6 9" stroke="#fff" fill="none"/></svg></span><span><svg width="8" height="10"><path d="M2 1 6 5 2 9" stroke="#fff" fill="none"/></svg></span></div>
  <div class="shelf">
    <div class="product"><div class="ph" role="img" aria-label="Product photo of a black supplement tub"></div><div class="row"><span>Duis aute irure dolor</span><span class="price">£200.00</span></div><div class="row sub"><svg width="60" height="11"><g fill="#f0a020"><use href="#s"/><use href="#s" x="12"/><use href="#s" x="24"/></g><g fill="#ddd"><use href="#s" x="36"/><use href="#s" x="48"/></g></svg><span class="old">£300.00</span></div></div>
    <div class="product"><div class="ph" role="img" aria-label="Product photo of a white supplement tub"></div><div class="row"><span>Duis aute irure dolor</span><span class="price">£200.00</span></div><div class="row sub"><svg width="60" height="11"><g fill="#f0a020"><use href="#s"/><use href="#s" x="12"/><use href="#s" x="24"/></g><g fill="#ddd"><use href="#s" x="36"/><use href="#s" x="48"/></g></svg><span class="old">£300.00</span></div></div>
    <div class="product"><div class="ph" role="img" aria-label="Product photo of a white tub with a dark label"></div><div class="row"><span>Duis aute irure dolor</span><span class="price">£200.00</span></div><div class="row sub"><svg width="60" height="11"><g fill="#f0a020"><use href="#s"/><use href="#s" x="12"/><use href="#s" x="24"/></g><g fill="#ddd"><use href="#s" x="36"/><use href="#s" x="48"/></g></svg><span class="old">£300.00</span></div></div>
    <div class="product"><div class="ph" role="img" aria-label="Product photo of a plain white supplement tub"></div><div class="row"><span>Duis aute irure dolor</span><span class="price">£200.00</span></div><div class="row sub"><svg width="60" height="11"><g fill="#f0a020"><use href="#s"/><use href="#s" x="12"/><use href="#s" x="24"/></g><g fill="#ddd"><use href="#s" x="36"/><use href="#s" x="48"/></g></svg><span class="old">£300.00</span></div></div>
  </div>
</section>

<section class="faq">
  <h3 class="col-title">WHAT ELSE SHOULD I KNOW?</h3>
  <div class="faq-cols">
    <div class="faq-item"><h4>Nemo Enim Ipsam Voluptatem ?</h4><p>Vivamus elementum semper nisi. Lorem ipsum met, sectetuer adipiscing elit. Aenean commodoVivamus elementum semper nisi.</p><div class="more"><svg width="10" height="10"><circle cx="5" cy="5" r="5" fill="#444"/><path d="M4 2.5 6.5 5 4 7.5" stroke="#fff" fill="none"/></svg>READ MORE</div></div>
    <div class="faq-item"><h4>Nemo Enim Ipsam Voluptatem ?</h4><p>Vivamus elementum semper nisi. Lorem ipsum met, sectetuer adipiscing elit. Aenean commodoVivamus elementum semper nisi.</p><div class="more"><svg width="10" height="10"><circle cx="5" cy="5" r="5" fill="#444"/><path d="M4 2.5 6.5 5 4 7.5" stroke="#fff" fill="none"/></svg>READ MORE</div></div>
    <div class="faq-item"><h4>Nemo Enim Ipsam Voluptatem ?</h4><p>Vivamus elementum semper nisi. Lorem ipsum met, sectetuer adipiscing elit. Aenean commodoVivamus elementum semper nisi.</p><div class="more"><svg width="10" height="10"><circle cx="5" cy="5" r="5" fill="#444"/><path d="M4 2.5 6.5 5 4 7.5" stroke="#fff" fill="none"/></svg>READ MORE</div></div>
  </div>
</section>

<footer class="footer">
  <div class="brand"><span class="brand-dot"></span>BRISKO</div>
  <div class="contact" style="left:352px"><span class="ic"><svg width="12" height="16" viewBox="0 0 12 16"><path d="M6 0a6 6 0 0 1 6 6c0 4-6 10-6 10S0 10 0 6a6 6 0 0 1 6-6z" fill="#fff"/><circle cx="6" cy="6" r="2" fill="#222"/></svg></span><span>212 Larkfield (Cnr. Ashby &amp;<br>Rowan St.) Easton, VIC.</span></div>
  <div class="contact" style="left:660px"><span class="ic"><svg width="14" height="14" viewBox="0 0 14 14"><path d="M3 1l2 3-1.5 1.5a8 8 0 0 0 5 5L10 9l3 2-1 2C6 13 1 8 1 2z" fill="#fff"/></svg></span><span>Phone :<br><b style="font-weight:600">+1 1300 555 014</b></span></div>
  <div class="contact" style="left:900px"><span class="ic"><svg width="14" height="10" viewBox="0 0 14 10"><rect x=".5" y=".5" width="13" height="9" fill="none" stroke="#fff"/><path d="M.5.5 7 6 13.5.5" stroke="#fff" fill="none"/></svg></span><span>E-mail:<br>info@brisko.com</span></div>
  <div class="rule"></div>
  <div class="newsletter">NEWSLETTER SIGNUP</div>
  <div class="email"><span>Enter your email address</span><svg width="16" height="14" viewBox="0 0 16 14"><path d="M0 6 16 0 12 14 8 9z" fill="#fff"/></svg></div>
  <div class="links"><span>HOME</span>/<span>PRODUCT</span>/<span>TRAINER</span>/<span>BLOG</span>/<span>FAQS</span>/<span>TERMS OF USE</span>/<span>CONTACT</span></div>
  <div class="social"><span></span><span></span><span></span><span></span><span></span></div>
</footer>

<div class="copy">©2014 - 2015 Brisko., All Rights Reserved.</div>

</body>
</html>
```